Personal loan pre-approval

We are a credit union sending out pre-approvals for personal loans. I am attaching a letter that we sent out during previous pre-approvals. The fine print needs to be included on the postcard from the letter, but the rest is just a guide. The theme I'm thinking of may be Easy, Cold Hard Cash, but I'm not stuck on it. Thanks.

http://www.brightleafprint.com/gallerydetail.aspx?sectionID=143&photoID=104

The cash banner is an example of what I had in mind.

We don't want the actual letter on the postcard, it was meant to be a guide only as to what we are selling. The front page should be explaining that they are pre-approved for a personal loan, say up $10,000, at a rate of 7.99% APR*. It should be mentioned how they are pre-approved, which means no credit check, no proof of income needed. Somewhere, either on the front or the back, needs to be the fine print in a discreet fashion. look at the link I provide for some guidance. Thanks!
Updates

Industry/Entity Type

Union

Requirements
Must have
• Must have fine print on postcard that is on example letter.
Should not have
• Should not have the entire letter on the postcard

```html
<!DOCTYPE html>
<html lang="en">
<head>
<meta charset="utf-8">
<title>Pre-Approved Signature Loan Postcards</title>
<link rel="stylesheet" href="https://fonts.googleapis.com/css2?family=Arimo:wght@400;700&family=Roboto+Condensed:wght@700;900&family=Tinos&display=swap">
<style>
  :root {
    --sheet: #000000;
    --navy: #2a3a86;
    --navy-deep: #22307a;
    --white: #ffffff;
    --ink: #1f2a5c;
    --photo-top: #c9a3cf;
    --photo-mid: #e9d6dc;
    --photo-low: #d8c2a4;
  }
  * { margin: 0; padding: 0; box-sizing: border-box; }
  html, body { width: 1200px; height: 783px; overflow: hidden; background: var(--sheet); }
  .sheet { position: relative; width: 1200px; height: 783px; }

  .postcard {
    position: absolute; width: 581px; height: 376px; overflow: hidden;
    font-family: "Arimo", Arial, sans-serif;
  }
  .postcard.tl { left: 0; top: 0; }
  .postcard.tr { left: 619px; top: 0; }
  .postcard.bl { left: 0; top: 407px; }
  .postcard.br { left: 619px; top: 407px; }

  .photo {
    position: absolute; inset: 0;
    background:
      radial-gradient(ellipse 160px 120px at 80px 120px, rgba(235,200,180,.8), transparent 70%),
      radial-gradient(ellipse 220px 110px at 430px 250px, rgba(240,210,190,.75), transparent 70%),
      linear-gradient(180deg, var(--photo-top) 0%, var(--photo-mid) 45%, var(--photo-low) 100%);
  }

  .outlined {
    color: var(--white);
    -webkit-text-stroke: 3px var(--navy);
    paint-order: stroke fill;
  }

  .headline {
    position: absolute; left: 19px; top: 34px;
    font-family: "Roboto Condensed", "Arial Narrow", sans-serif; font-weight: 700;
    white-space: nowrap; line-height: 1;
  }
  .headline .lead { font-size: 21px; }
  .headline .key { font-size: 29px; font-weight: 900; }

  .amount, .product {
    position: absolute; left: 19px;
    font-family: "Arimo", Arial, sans-serif; font-weight: 700;
    line-height: 1; letter-spacing: -1px; white-space: nowrap;
  }
  .amount { top: 92px; font-size: 50px; }
  .product { top: 143px; font-size: 50px; }

  .terms {
    position: absolute; left: 184px; top: 196px;
    font-size: 11px; line-height: 15px; color: var(--ink);
  }

  .issuer { position: absolute; left: 374px; top: 10px; width: 200px; color: var(--navy); }
  .issuer .mark {
    position: absolute; left: 0; top: 8px; width: 44px; height: 44px; background: var(--navy);
  }
  .issuer .name {
    position: absolute; left: 54px; top: 2px;
    font-family: "Arimo", Arial, sans-serif; font-weight: 400;
    font-size: 15px; line-height: 19px; white-space: nowrap;
  }
  .issuer .contact {
    position: absolute; left: 9px; top: 68px;
    font-size: 10px; white-space: nowrap; word-spacing: 3px;
  }

  .rate-band { position: absolute; left: 0; bottom: 0; width: 390px; height: 55px; }
  .rate-band svg { position: absolute; inset: 0; }
  .rate-text {
    position: absolute; left: 32px; bottom: 10px;
    font-family: "Tinos", "Times New Roman", serif; color: var(--white); white-space: nowrap;
  }
  .rate-text .label { font-size: 14px; margin-right: 6px; }
  .rate-text .value { font-size: 37px; letter-spacing: 1.5px; }

  .fine-print {
    position: absolute; right: 10px; bottom: 6px; width: 180px;
    font-size: 7px; line-height: 9px; color: var(--ink); text-align: right;
  }
</style>
</head>
<body>
<main class="sheet">

  <section class="postcard tl">
    <div class="photo" role="img" aria-label="Photo of hands writing a cheque with a fountain pen beside a stack of cash"></div>
    <p class="headline outlined"><span class="lead">You have been </span><span class="key">PRE-APPROVED</span></p>
    <p class="amount outlined">$7,000</p>
    <p class="product outlined">Signature Loan</p>
    <p class="terms">including existing loan balances*<br>Up to 60 month term</p>
    <div class="issuer">
      <span class="mark"></span>
      <p class="name">Harbor Valley<br>TEACHERS<br>CREDIT UNION</p>
      <p class="contact">Tel: 415-555-0148 www.hvteachcu.org</p>
    </div>
    <div class="rate-band">
      <svg width="390" height="55" viewBox="0 0 390 55"><polygon points="0,0 350,0 382,55 0,55" fill="var(--navy-deep)"/></svg>
      <p class="rate-text"><span class="label">Fixed rate at</span><span class="value">9.99% APR</span></p>
    </div>
    <p class="fine-print">*Total includes existing loan balances. No credit check or proof of income needed. Offer subject to membership terms.</p>
  </section>

  <section class="postcard tr">
    <div class="photo" role="img" aria-label="Photo of hands writing a cheque with a fountain pen beside a stack of cash"></div>
    <p class="headline outlined"><span class="lead">You have been </span><span class="key">PRE-APPROVED</span></p>
    <p class="amount outlined">$2,000</p>
    <p class="product outlined">Signature Loan</p>
    <p class="terms">including existing loan balances*<br>Up to 60 month term</p>
    <div class="issuer">
      <span class="mark"></span>
      <p class="name">Harbor Valley<br>TEACHERS<br>CREDIT UNION</p>
      <p class="contact">Tel: 415-555-0148 www.hvteachcu.org</p>
    </div>
    <div class="rate-band">
      <svg width="390" height="55" viewBox="0 0 390 55"><polygon points="0,0 350,0 382,55 0,55" fill="var(--navy-deep)"/></svg>
      <p class="rate-text"><span class="label">Fixed rate at</span><span class="value">13.99% APR</span></p>
    </div>
    <p class="fine-print">*Total includes existing loan balances. No credit check or proof of income needed. Offer subject to membership terms.</p>
  </section>

  <section class="postcard bl">
    <div class="photo" role="img" aria-label="Photo of hands writing a cheque with a fountain pen beside a stack of cash"></div>
    <p class="headline outlined"><span class="lead">You have been </span><span class="key">PRE-APPROVED</span></p>
    <p class="amount outlined">$10,000</p>
    <p class="product outlined">Signature Loan</p>
    <p class="terms">including existing loan balances*<br>Up to 60 month term</p>
    <div class="issuer">
      <span class="mark"></span>
      <p class="name">Harbor Valley<br>TEACHERS<br>CREDIT UNION</p>
      <p class="contact">Tel: 415-555-0148 www.hvteachcu.org</p>
    </div>
    <div class="rate-band">
      <svg width="390" height="55" viewBox="0 0 390 55"><polygon points="0,0 350,0 382,55 0,55" fill="var(--navy-deep)"/></svg>
      <p class="rate-text"><span class="label">Fixed rate at</span><span class="value">7.99% APR</span></p>
    </div>
    <p class="fine-print">*Total includes existing loan balances. No credit check or proof of income needed. Offer subject to membership terms.</p>
  </section>

  <section class="postcard br">
    <div class="photo" role="img" aria-label="Photo of hands writing a cheque with a fountain pen beside a stack of cash"></div>
    <p class="headline outlined"><span class="lead">You have been </span><span class="key">PRE-APPROVED</span></p>
    <p class="amount outlined">$4,000</p>
    <p class="product outlined">Signature Loan</p>
    <p class="terms">including existing loan balances*<br>Up to 60 month term</p>
    <div class="issuer">
      <span class="mark"></span>
      <p class="name">Harbor Valley<br>TEACHERS<br>CREDIT UNION</p>
      <p class="contact">Tel: 415-555-0148 www.hvteachcu.org</p>
    </div>
    <div class="rate-band">
      <svg width="390" height="55" viewBox="0 0 390 55"><polygon points="0,0 350,0 382,55 0,55" fill="var(--navy-deep)"/></svg>
      <p class="rate-text"><span class="label">Fixed rate at</span><span class="value">11.99% APR</span></p>
    </div>
    <p class="fine-print">*Total includes existing loan balances. No credit check or proof of income needed. Offer subject to membership terms.</p>
  </section>

</main>
</body>
</html>
```